I need the Scorecard I've developed for my staff to be produced into a visually engaging piece that will encourage the staff to utilize it on a daily basis. I'm thinking it could be 5x7 in size so that it isn't too cumbersome, but I'm open to different layouts.
I have multiple other departments that will need Scorecards created for them as well, but each one will contain task specific questions for each department.

```html
<!DOCTYPE html>
<html lang="en">
<head>
<meta charset="utf-8">
<title>Receptionist Daily Excellence Scorecard</title>
<link href="https://fonts.googleapis.com/css2?family=Arimo:wght@400;700&family=Roboto+Condensed:wght@400;700&display=swap" rel="stylesheet">
<style>
  :root {
    --frame-red: #e0282c;
    --title-blue: #004b93;
    --band-grey: #5f5b5a;
    --ink: #1d1d1b;
    --rate-red: #d7262e;
    --rate-blue: #1a9ad6;
    --rate-green: #14913e;
    --blue-head: #99d0f2;
    --blue-row: #d0e7f8;
    --gold-head: #e5cc80;
    --gold-row: #fbeaa4;
    --lilac-head: #c1b8d9;
    --lilac-row: #e3dfef;
    --rose-head: #e29ab0;
    --rose-row: #f8d7e6;
  }
  * { box-sizing: border-box; margin: 0; padding: 0; }
  html, body { width: 1057px; height: 1200px; overflow: hidden; background: #fff; }
  .scorecard {
    position: relative; width: 1057px; height: 1200px; overflow: hidden;
    border: 3px solid var(--frame-red); background: #fff;
    font-family: "Arimo", Arial, sans-serif; color: var(--ink);
  }
  .title {
    position: absolute; left: 26px; top: 14px;
    font-family: "Roboto Condensed", sans-serif; font-size: 58px; line-height: 64px;
    color: var(--title-blue); font-weight: 400; white-space: nowrap; letter-spacing: -0.3px;
    transform: scaleX(0.895); transform-origin: left top;
  }
  .title strong { font-weight: 700; }
  .field {
    position: absolute; left: 26px; width: 562px; height: 35px;
    border: 2px solid #555; font-size: 21px; padding: 3px 0 0 10px;
  }
  .field.name { top: 79px; }
  .field.location { top: 121px; }
  .field .date { position: absolute; left: 350px; }
  .rating-key {
    position: absolute; left: 600px; top: 79px; width: 426px; height: 77px;
    border: 2px solid #555; text-align: center;
  }
  .rating-key .prompt { font-size: 19px; margin-top: 12px; }
  .rating-key .scale {
    font-family: "Roboto Condensed", sans-serif; font-size: 17px; margin-top: 11px;
    display: flex; justify-content: space-between; padding: 0 8px; white-space: nowrap;
  }
  .scale .low { color: var(--rate-red); }
  .scale .mid { color: var(--rate-blue); }
  .scale .high { color: var(--rate-green); }

  .section { position: absolute; left: 26px; width: 1000px; }
  .section-band {
    position: relative; height: 38px; background: var(--band-grey);
    border-radius: 22px 22px 0 0; color: #fff; font-weight: 700; font-size: 26px;
    text-align: center; line-height: 40px; margin-bottom: 3px;
  }
  .section-band svg { position: absolute; }
  .grid {
    display: grid; grid-template-columns: 454px 125px 417px; gap: 2px;
  }
  .grid > div { height: 38px; }
  .grid .head { font-size: 22px; line-height: 40px; color: #2b2b2b; }
  .grid .head.task { padding-left: 18px; }
  .grid .head.rating {
    font-family: "Roboto Condensed", sans-serif; font-size: 21px; padding-left: 4px; line-height: 34px;
    white-space: nowrap; overflow: visible;
  }
  .grid .head.rating span { display: inline-block; transform: scaleX(0.83); transform-origin: left center; }
  .grid .head.notes { text-align: center; }
  .grid .cell.task { font-size: 20.5px; line-height: 38px; padding-left: 18px; white-space: nowrap; }

  .calls .head { background: var(--blue-head); } .calls .cell { background: var(--blue-row); }
  .busy .head { background: var(--gold-head); } .busy .cell { background: var(--gold-row); }
  .sched .head { background: var(--lilac-head); } .sched .cell { background: var(--lilac-row); }
  .care .head { background: var(--rose-head); } .care .cell { background: var(--rose-row); }
</style>
</head>
<body>
<main class="scorecard">
  <h1 class="title"><strong>RECEPTIONIST</strong> DAILY EXCELLENCE SCORECARD</h1>
  <div class="field name">Name :</div>
  <div class="field location">Location :<span class="date">Date :</span></div>
  <div class="rating-key">
    <p class="prompt">Please Rate yourself for each task</p>
    <p class="scale"><span class="low">1 = Needs Improvement</span><span class="mid">3 = Meets Expectations</span><span class="high">5 = Excellent</span></p>
  </div>

  <section class="section calls" style="top:172px">
    <div class="section-band">
      <svg style="left:215px;top:-6px" width="34" height="38" viewBox="0 0 34 38" aria-hidden="true">
        <rect x="1" y="4" width="26" height="33" fill="#1a7fd0"/>
        <g fill="#1a7fd0"><rect x="4" y="0" width="2" height="5"/><rect x="9" y="0" width="2" height="5"/><rect x="14" y="0" width="2" height="5"/><rect x="19" y="0" width="2" height="5"/><rect x="24" y="0" width="2" height="5"/></g>
        <g stroke="#fff" stroke-width="2"><line x1="5" y1="12" x2="22" y2="12"/><line x1="5" y1="18" x2="18" y2="18"/><line x1="5" y1="24" x2="15" y2="24"/><line x1="5" y1="30" x2="13" y2="30"/></g>
        <path d="M17 30 L30 14 L33 17 L20 32 L16 33 Z" fill="#1a7fd0" stroke="#fff" stroke-width="1.5"/>
      </svg>
      1. Call Handling &amp; First Call Intake
    </div>
    <div class="grid">
      <div class="head task">Task</div><div class="head rating"><span>Self Rating (1-5)</span></div><div class="head notes">Notes / Issues</div>
      <div class="cell task">Answered 90%+ calls within 3 rings</div><div class="cell"></div><div class="cell"></div>
      <div class="cell task">Maintained empathy and professionalism</div><div class="cell"></div><div class="cell"></div>
      <div class="cell task">Accurately completed all First Call fields</div><div class="cell"></div><div class="cell"></div>
      <div class="cell task">Worked within Receptionist role</div><div class="cell"></div><div class="cell"></div>
    </div>
  </section>

  <section class="section busy" style="top:423px">
    <div class="section-band">
      <svg style="left:184px;top:-5px" width="26" height="40" viewBox="0 0 26 40" aria-hidden="true">
        <path d="M6 2 C2 2 1 6 2 12 C4 22 9 32 16 38 C18 40 22 39 24 36 L20 30 C18 31 16 32 15 31 C11 26 9 20 8 14 C8 12 10 11 12 11 L10 3 Z" fill="#ef7d22"/>
      </svg>
      2. Call Management During Busy Times
    </div>
    <div class="grid">
      <div class="head task">Task</div><div class="head rating"><span>Self Rating (1-5)</span></div><div class="head notes">Notes / Issues</div>
      <div class="cell task">Prioritized urgent vs. non-urgent calls</div><div class="cell"></div><div class="cell"></div>
      <div class="cell task">Hold times under 1 minute</div><div class="cell"></div><div class="cell"></div>
      <div class="cell task">Logged all calls</div><div class="cell"></div><div class="cell"></div>
      <div class="cell task">Requested help if overwhelmed</div><div class="cell"></div><div class="cell"></div>
    </div>
  </section>

  <section class="section sched" style="top:679px">
    <div class="section-band">
      <svg style="left:263px;top:-9px" width="44" height="42" viewBox="0 0 44 42" aria-hidden="true">
        <rect x="1" y="5" width="42" height="36" fill="#c1b8d9" stroke="#7a6aae" stroke-width="2"/>
        <rect x="1" y="5" width="42" height="8" fill="#7a6aae"/>
        <rect x="7" y="0" width="4" height="9" fill="#fff" stroke="#7a6aae" stroke-width="1.5"/>
        <rect x="33" y="0" width="4" height="9" fill="#fff" stroke="#7a6aae" stroke-width="1.5"/>
        <g fill="#7a6aae">
          <rect x="8" y="17" width="5" height="4"/><rect x="16" y="17" width="5" height="4"/><rect x="24" y="17" width="5" height="4"/><rect x="32" y="17" width="5" height="4"/>
          <rect x="8" y="24" width="5" height="4"/><rect x="16" y="24" width="5" height="4"/><rect x="24" y="24" width="5" height="4"/><rect x="32" y="24" width="5" height="4"/>
          <rect x="8" y="31" width="5" height="4"/><rect x="16" y="31" width="5" height="4"/><rect x="24" y="31" width="5" height="4"/><rect x="32" y="31" width="5" height="4"/>
        </g>
      </svg>
      3. Scheduling Accuracy
    </div>
    <div class="grid">
      <div class="head task">Task</div><div class="head rating"><span>Self Rating (1-5)</span></div><div class="head notes">Notes / Issues</div>
      <div class="cell task">Updated scheduling board</div><div class="cell"></div><div class="cell"></div>
      <div class="cell task">Cross-checked with Red Book</div><div class="cell"></div><div class="cell"></div>
      <div class="cell task">Entered manifold info promptly</div><div class="cell"></div><div class="cell"></div>
    </div>
  </section>

  <section class="section care" style="top:892px">
    <div class="section-band">
      <svg style="left:297px;top:-7px" width="38" height="40" viewBox="0 0 38 40" aria-hidden="true">
        <path d="M12 1 C15 5 23 5 26 1 L37 7 L34 16 L29 14 L29 39 L9 39 L9 14 L4 16 L1 7 Z" fill="#b8396e"/>
      </svg>
      4. Clothing &amp; Flowers
    </div>
    <div class="grid">
      <div class="head task">Task</div><div class="head rating"><span>Self Rating (1-5)</span></div><div class="head notes">Notes / Issues</div>
      <div class="cell task">Clothing sheet completed</div><div class="cell"></div><div class="cell"></div>
      <div class="cell task">Family contact noted on sheet</div><div class="cell"></div><div class="cell"></div>
      <div class="cell task">Floral deliveries logged</div><div class="cell"></div><div class="cell"></div>
      <div class="cell task">Concerns communicated to Care Center</div><div class="cell"></div><div class="cell"></div>
      <div class="cell task">Flower placement verified</div><div class="cell"></div><div class="cell"></div>
    </div>
  </section>
</main>
</body>
</html>
```